2 x Digitize Logo | 2 x Business Cards | 2 x Fridge Magnets

We require 6 deliverables:
1. Residential logo redrawn (same just high quality for large print format).
2. Corporate logo redrawn (minor changes to wording and high quality for large print format).
3. New business card design for Furniture Removals (residential)
4. New business card design for Corporate Relocations (business)
5. New Fridge magnet for Furniture removals (residential)
6. New fridge magnet for Corporate Relocations (business)
1. Residential Logo
a. We require the logo to be translated into a high quality digital image with no modifications.
(see attached resilogo.jpg)
2. Residential Logo
a. We require the logo to be edited (add the word corporate relocations) be translated into a high quality digital image.
(see attached corplogo.jpg)
3. Using the resilogo please make a new business card for our business.
a. Please see the web site https://www.larkbendcarters.com.au for colours and inspiration.
b. The residential business card needs the following information:
i. Business Name (using the residential logo).
ii. Free Call: 1800 LB Cart (the L, B and Cart much be the same colour as the logo).
iii. Website: www.LarkbendCarters.com.au
iv. Address: 4/17 Ormsdale Court, VIC 3264
v. Email: cart@LarkbendCarters.com.au
vi. backof Card:
Review our service
www.PennantOrbit.com.au
Services: Local, Country, Interstate | Furniture Removals | Piano, Billiard Tables & Antiques
4. Using the corplogo please make a new business card for our business.
b. The corporate business card needs the following information:
i. Business Name (using the corporate logo).
v. Email: corporate@LarkbendCarters.com.au
vi. Back of Card:
Review our service
www.PennantOrbit.com.au
Services: Corporate relocations | Office equipment moves | Packing Service | Packing Materials
5. Using the resilogo please make a new fridge magent for our business.
b. The residential fidge magnet needs the following information:
iv. Services: Local, Country, Interstate | Furniture Removals | Piano, Billiard Tables & Antiques
6. Using the corplogo please make a new fridge magent for our business.
b. The corporate fidge magnet needs the following information:
iv. Services: Local, Country, Interstate | Corporate relocations
Target Market(s)
Residential Furniture Removals and Corporate Office relocations
Industry/Entity Type
Business
Contact Information for Business Card
Please see full brief for six items required
Requirements
Must have
- Clean simple, easy to read
Nice to have
- fresh, stand out, eye catching
Should not have
- plain, standard, boring, general

```html
<!DOCTYPE html>
<html lang="en">
<head>
<meta charset="utf-8">
<title>Larkbend Carters – Business Card</title>
<link rel="stylesheet" href="https://fonts.googleapis.com/css2?family=Open+Sans:wght@400;600;800&display=swap">
<style>
  :root {
    --backdrop: #3b3531;
    --card: #0e0e0e;
    --ink: #f2f2f2;
    --muted: #d8d8d8;
    --yellow: #f4b800;
    --red: #e4252a;
    --green: #23a84b;
    --silver: #c9c9c9;
  }
  * { box-sizing: border-box; margin: 0; padding: 0; }
  html, body { width: 1200px; height: 900px; overflow: hidden; }
  body {
    background: var(--backdrop);
    font-family: "Open Sans", Arial, sans-serif;
    color: var(--ink);
    position: relative;
  }
  .card {
    position: absolute;
    top: 295px;
    width: 530px;
    height: 310px;
    background: var(--card);
    border-radius: 4px;
    box-shadow: 0 8px 22px rgba(0,0,0,.45);
  }
  .card--front { left: 50px; }
  .card--back { left: 620px; }

  .wordmark {
    position: absolute;
    font-weight: 800;
    letter-spacing: .5px;
    text-transform: uppercase;
    white-space: nowrap;
  }
  .card--front .wordmark {
    left: 40px; top: 70px;
    font-size: 40px;
    color: var(--yellow);
  }
  .card--back .wordmark {
    left: 60px; top: 40px;
    font-size: 34px;
    color: var(--silver);
  }

  .contact-list {
    position: absolute;
    left: 40px; top: 170px;
    list-style: none;
    font-size: 17px;
    line-height: 26px;
  }
  .contact-list li { display: flex; align-items: center; gap: 10px; }
  .contact-list li.address { margin-top: 12px; }
  .contact-list svg { width: 14px; height: 14px; flex: none; }
  .tone-yellow { color: var(--yellow); }
  .tone-red { color: var(--red); }
  .tone-green { color: var(--green); }

  .review {
    position: absolute;
    left: 300px; top: 100px;
    text-align: center;
    font-size: 12px;
    line-height: 20px;
    color: var(--muted);
    transform: translateX(-50%);
  }
  .services {
    position: absolute;
    left: 60px; top: 170px;
    font-size: 13px;
    line-height: 20px;
  }
  .services h2 {
    font-size: 13px;
    font-weight: 400;
    color: var(--yellow);
    margin-bottom: 2px;
  }
  .services ul { list-style: none; }
  .services li { display: flex; align-items: center; gap: 8px; }
  .services li::before {
    content: "";
    width: 8px; height: 8px;
    border-radius: 50%;
    background: var(--yellow);
  }
</style>
</head>
<body>

<section class="card card--front" aria-label="Card front">
  <div class="wordmark">Larkbend Carters</div>
  <ul class="contact-list">
    <li>
      <svg viewBox="0 0 16 16" aria-hidden="true"><path fill="#f4b800" d="M3 1l3 3-2 2c1 2 3 4 5 5l2-2 3 3-2 3C7 14 2 9 1 3z"/></svg>
      <span>1800 <span class="tone-yellow">L</span><span class="tone-red">B</span> <span class="tone-green">Cart</span></span>
    </li>
    <li>
      <svg viewBox="0 0 16 16" aria-hidden="true"><rect x="1" y="3" width="14" height="10" fill="#f4b800"/><path d="M1 3l7 6 7-6" fill="none" stroke="#0e0e0e" stroke-width="1.4"/></svg>
      <span>cart@LarkbendCarters.com.au</span>
    </li>
    <li>
      <svg viewBox="0 0 16 16" aria-hidden="true"><circle cx="8" cy="8" r="7" fill="#f4b800"/><path d="M1 8h14M8 1c-3 4-3 10 0 14M8 1c3 4 3 10 0 14" fill="none" stroke="#0e0e0e" stroke-width="1"/></svg>
      <span>www.LarkbendCarters.com.au</span>
    </li>
    <li class="address">
      <svg viewBox="0 0 16 16" aria-hidden="true"><path fill="#f4b800" d="M8 0a5.5 5.5 0 0 0-5.5 5.5C2.5 10 8 16 8 16s5.5-6 5.5-10.5A5.5 5.5 0 0 0 8 0z"/><circle cx="8" cy="5.5" r="2" fill="#0e0e0e"/></svg>
      <span>4/17 Ormsdale Court, VIC 3264</span>
    </li>
  </ul>
</section>

<section class="card card--back" aria-label="Card back">
  <div class="wordmark">Larkbend Carters</div>
  <p class="review">REVIEW OUR SERVICE<br>www.PennantOrbit.com.au</p>
  <div class="services">
    <h2>SERVICES:</h2>
    <ul>
      <li>Local, Country, Interstate</li>
      <li>Furniture Removals</li>
      <li>Piano, Billiard Tables &amp; Antiques</li>
    </ul>
  </div>
</section>

</body>
</html>
```